Harborlight Amusement Collective (HAC)

We need a business card design for Harborlight Amusement Collective. Modern and sleek looking, with all critical information. Open to single or double sided designs, if double sided info needs to be all on one side. The main Logo is Harborlight Amusement collective and must be on the card. The other three logos are for the brands that fall under the group, they might be good on the back.

Industry/Entity Type

Business

```html
<!DOCTYPE html>
<html lang="en">
<head>
<meta charset="utf-8">
<title>Harborlight Amusement Collective – Business Card</title>
<link rel="stylesheet" href="https://fonts.googleapis.com/css2?family=Montserrat:wght@400;500;600;700&family=Oswald:wght@500&display=swap">
<style>
  :root {
    --navy: #24508f;
    --olive: #7d9a33;
    --ink: #2b2b2b;
    --card: #f1f1ee;
    --backdrop: #dcdcd8;
    --band-text: #d9dde6;
  }
  * { margin: 0; padding: 0; box-sizing: border-box; }
  html, body {
    width: 1200px; height: 1054px; overflow: hidden;
    background: var(--backdrop);
    font-family: "Montserrat", Arial, sans-serif;
  }
  .business-card {
    position: absolute; left: 50px; top: 194px;
    width: 1100px; height: 666px;
    background: var(--card);
    overflow: hidden;
    box-shadow: 0 10px 30px rgba(0,0,0,.15);
  }
  .wordmark {
    position: absolute; left: 63px; top: 62px; width: 778px;
    color: var(--navy); font-weight: 700; text-align: center;
  }
  .wordmark-main { font-size: 43px; letter-spacing: .5px; line-height: 1; white-space: nowrap; }
  .wordmark-sub {
    display: flex; align-items: center; gap: 26px; margin-top: 26px;
    font-size: 40px; letter-spacing: 14px; line-height: 1;
  }
  .wordmark-sub .rule { flex: 1; height: 4px; background: var(--navy); }
  .wordmark-sub span { padding-left: 14px; }
  .brand-dot {
    position: absolute; left: 71px; top: 375px;
    width: 190px; height: 190px; border-radius: 50%;
    background: var(--navy);
  }
  .contact { position: absolute; left: 573px; top: 278px; color: var(--ink); }
  .contact-name {
    font-family: "Oswald", "Arial Narrow", sans-serif; font-weight: 500;
    font-size: 42px; color: var(--navy); line-height: 1;
  }
  .contact-title { font-size: 25px; margin-top: 12px; font-weight: 500; }
  .contact-address { font-size: 25px; line-height: 38px; margin-top: 28px; font-weight: 500; }
  .contact-line {
    display: flex; align-items: center; gap: 22px;
    font-size: 25px; font-weight: 500; height: 40px;
  }
  .contact-lines { margin-top: 16px; }
  .contact-line svg { width: 32px; height: 24px; fill: var(--ink); }
  .olive-bar {
    position: absolute; left: 0; bottom: 0; width: 470px; height: 26px;
    background: var(--olive);
  }
  .navy-band {
    position: absolute; right: 0; bottom: 0; width: 673px; height: 85px;
    background: var(--navy);
    clip-path: polygon(52px 0, 100% 0, 100% 100%, 0 100%);
  }
  .web-address {
    position: absolute; left: 573px; bottom: 22px;
    font-size: 26px; font-weight: 500; color: var(--band-text);
  }
</style>
</head>
<body>
  <div class="business-card">
    <div class="wordmark">
      <div class="wordmark-main">HARBORLIGHT AMUSEMENT</div>
      <div class="wordmark-sub"><i class="rule"></i><span>COLLECTIVE</span><i class="rule"></i></div>
    </div>

    <div class="brand-dot" aria-hidden="true"></div>

    <div class="contact">
      <div class="contact-name">Marina Kessel</div>
      <div class="contact-title">Managing Director</div>
      <div class="contact-address">87 Quayside Ave., Port<br>Linden, US 540812</div>
      <div class="contact-lines">
        <div class="contact-line">
          <svg viewBox="0 0 32 24" aria-label="Phone"><path d="M3 7c0-3 6-5 13-5s13 2 13 5v2h-6V6.5c-2-.7-4.5-1-7-1s-5 .3-7 1V9H3z"/><path d="M9 10h14l4 11H5z"/></svg>
          <span>555.204.7781</span>
        </div>
        <div class="contact-line">
          <svg viewBox="0 0 32 24" aria-label="Email"><path d="M4 4h24v16H4z M6 6v1l10 7 10-7V6z"/></svg>
          <span>mkessel@harborlightac.com</span>
        </div>
      </div>
    </div>

    <div class="olive-bar"></div>
    <div class="navy-band"></div>
    <div class="web-address">www.harborlightac.com</div>
  </div>
</body>
</html>
```